Larkfield Ridge Management

I need a professional website. My current website is larkfieldridgemanagement.com and I hate it. It was created with some AI tool very quickly because I needed a site up and running with no advanced notice. I’m open to all designs .. I trust you, the professionals will deliver the results I’m anxiously awaiting! :)

```html
<!DOCTYPE html>
<html lang="en">
<head>
<meta charset="utf-8">
<title>Larkfield Ridge Management</title>
<link href="https://fonts.googleapis.com/css2?family=Lexend:wght@300;400;500&family=Poppins:wght@400;500;600&display=swap" rel="stylesheet">
<style>
:root{
  --red:#d52b2b;
  --navy:#1f3354;
  --navy-dark:#17263f;
  --ink:#222a36;
  --muted:#5b6270;
  --light:#f3f3f4;
  --line:#e1e2e6;
  --card-dark:#4a4b4e;
  --white:#ffffff;
}
*{box-sizing:border-box;margin:0;padding:0}
html,body{width:1200px;height:5286px;overflow:hidden}
body{font-family:"Poppins",sans-serif;color:var(--ink);background:var(--white);position:relative}
h1,h2,h3,h4{font-family:"Lexend",sans-serif;font-weight:400}
.abs{position:absolute}
.label{font-size:12px;color:var(--red);text-transform:uppercase;letter-spacing:.5px}
.heading{font-size:32px;color:var(--navy-dark);line-height:1.25}
.center{text-align:center;left:0;width:1200px}
.btn{display:flex;height:42px;position:absolute}
.btn .txt{background:var(--red);color:#fff;font-size:11px;display:flex;align-items:center;padding:0 20px;height:100%}
.btn .star{background:var(--red);width:42px;margin-left:3px;display:flex;align-items:center;justify-content:center;height:100%}
.photo{position:absolute}
/* hero */
.hero{position:absolute;left:0;top:0;width:1200px;height:672px;background:linear-gradient(100deg,#2d2f2c 0%,#4c4a40 35%,#7d7a68 60%,#5d6a55 100%)}
.hero .shade{position:absolute;inset:0;background:linear-gradient(90deg,rgba(20,22,28,.7),rgba(20,22,28,.15) 65%,rgba(0,0,0,0))}
.logo{display:flex;align-items:center;gap:8px;font-family:"Lexend",sans-serif;font-weight:500;font-size:15px;letter-spacing:.5px}
.logo .mark{width:14px;height:14px;background:var(--red)}
.nav{position:absolute;top:34px;left:395px;display:flex;gap:38px;font-size:12px;color:#fff}
.nav .active{color:var(--red)}
.hero h1{position:absolute;left:92px;top:243px;font-size:45px;line-height:55px;color:#fff;font-weight:300}
.hero h1 span{color:var(--red)}
.hero p{position:absolute;left:92px;top:420px;width:430px;font-size:11px;line-height:17px;color:#f0f0f0}
/* features */
.features{position:absolute;top:672px;left:0;width:1200px;height:260px;background:var(--light)}
.feature{position:absolute;top:68px;width:195px;height:128px;background:#fff;border:1px solid var(--line);text-align:center;font-size:12px;line-height:16px;color:var(--ink)}
.feature .ic{margin:28px auto 10px;width:26px;height:26px}
.corner{position:absolute;right:0;bottom:0;width:0;height:0;border-left:12px solid transparent;border-bottom:12px solid var(--red)}
.corner-tl{position:absolute;left:0;top:0;width:0;height:0;border-right:22px solid transparent;border-top:22px solid var(--red)}
.corner-tr{position:absolute;right:0;top:0;width:0;height:0;border-left:24px solid transparent;border-top:24px solid var(--red)}
/* about */
.about-box{position:absolute;left:92px;top:995px;width:1018px;height:430px;border:1px solid var(--line)}
.about-text{position:absolute;left:628px;top:45px;width:360px}
.about-text h2{font-size:31px;line-height:42px;color:var(--navy-dark);margin:8px 0 14px}
.about-text p{font-size:10.5px;line-height:18px;color:var(--muted);margin-bottom:14px}
/* services */
.services{position:absolute;top:1490px;left:0;width:1200px;height:645px;background:var(--light)}
.svc{position:absolute;top:145px;height:365px;overflow:hidden}
.svc .cap{position:absolute;left:0;right:0;bottom:0;padding:18px 24px;color:#fff}
.svc .cap h3{font-size:19px}
.svc .cap p{font-size:10px;line-height:14px;margin-top:4px}
.arrow-circle{position:absolute;width:38px;height:38px;border:1.5px solid var(--ink);border-radius:50%;display:flex;align-items:center;justify-content:center}
/* why */
.why{position:absolute;left:88px;top:2195px;width:1022px;height:455px}
.why .bar{position:absolute;left:0;top:0;width:30px;height:100%;background:var(--navy)}
.why-card{position:absolute;left:67px;top:42px;width:385px;height:380px;background:#fff;padding:42px 28px}
.why-card h2{font-size:32px;line-height:41px;color:var(--navy-dark);margin:6px 0 18px}
.why-card li{list-style:none;font-size:12px;color:var(--navy);display:flex;align-items:center;gap:10px;height:29px}
.why-card li::before{content:"";width:6px;height:6px;border-radius:50%;background:var(--red)}
/* gallery */
.gallery{position:absolute;top:2720px;left:0;width:1200px;height:695px;background:var(--light)}
/* faq */
.faq-box{position:absolute;left:92px;top:3470px;width:1018px;height:455px;border:1px solid var(--line)}
.faq-left{position:absolute;left:22px;top:28px;width:380px}
.faq-left h2{font-size:32px;line-height:38px;color:var(--navy-dark);margin:6px 0 22px}
.faq-open{background:var(--navy);color:#fff;padding:14px 14px 14px 30px;height:94px;position:relative;margin-bottom:16px}
.faq-open h4{font-family:"Poppins",sans-serif;font-size:12px;font-weight:500}
.faq-open p{font-size:10px;line-height:15px;margin-top:6px}
.faq-item{height:36px;border:1px solid var(--line);display:flex;align-items:center;padding:0 14px 0 30px;font-size:12px;color:var(--navy);margin-bottom:10px;position:relative;justify-content:space-between}
.faq-item::before,.faq-open::before{content:"";position:absolute;left:14px;top:50%;margin-top:-3px;width:6px;height:6px;border-radius:50%;background:var(--red)}
.faq-open::before{top:24px;background:#fff}
/* reviews */
.review{position:absolute;top:4065px;width:330px;height:200px;background:var(--card-dark);color:#fff;padding:22px 26px}
.review .who{display:flex;gap:12px;align-items:center;margin-bottom:14px}
.review .av{width:36px;height:36px;border-radius:50%;background:#b98a74;border:2px solid #fff}
.review .who span{font-size:12px;display:block}
.review .stars{color:#f2b51c;font-size:11px;letter-spacing:2px}
.review p{font-size:10px;line-height:16px;color:#eaeaea}
.review .q{position:absolute;right:20px;top:14px;font-family:"Lexend",sans-serif;font-size:56px;color:#6a6b6e;line-height:1}
/* cta */
.cta{position:absolute;top:4335px;left:0;width:1200px;height:585px;background:linear-gradient(180deg,#d7e7f4 0%,#e9eff3 30%,#9fb1a0 62%,#6d6f63 80%,#8a4e3c 100%)}
.cta h2{position:absolute;top:60px;left:0;width:1200px;text-align:center;font-size:40px;line-height:48px;color:var(--navy-dark)}
.cta p{position:absolute;top:158px;left:350px;width:500px;text-align:center;font-size:11px;line-height:17px;color:var(--navy)}
/* footer */
.footer{position:absolute;top:4920px;left:0;width:1200px;height:366px}
.footer h4{font-size:13px;color:var(--navy-dark);margin-bottom:16px}
.footer .links a{display:block;font-size:10px;color:var(--muted);text-decoration:none;line-height:21px}
.footer .contact div{display:flex;align-items:center;gap:10px;font-size:10px;color:var(--muted);margin-bottom:18px}
.footer .icon{width:20px;height:20px;border:1px solid var(--ink);border-radius:50%;display:flex;align-items:center;justify-content:center}
.footer input{width:205px;height:36px;border:1px solid #cfd1d6;font-size:10px;padding:0 16px;font-family:"Poppins",sans-serif}
</style>
</head>
<body>

<!-- Hero -->
<section class="hero">
  <div class="photo" role="img" aria-label="Property manager in a suit holding a tablet in front of a large suburban house" style="inset:0;background:linear-gradient(100deg,#3a3b36 0%,#5b5a4f 40%,#8a8774 62%,#536248 100%)"></div>
  <div class="shade"></div>
  <div class="abs logo" style="left:92px;top:28px;color:#fff"><span class="mark"></span>LARKFIELD</div>
  <nav class="nav">
    <span class="active">Home</span><span>About Us ⌄</span><span>Services ⌄</span><span>Resources</span><span>FAQs</span>
  </nav>
  <div class="btn" style="left:975px;top:22px;height:40px"><span class="txt" style="font-size:11px">Contact Us</span><span class="star" style="width:40px"><svg width="14" height="14" viewBox="0 0 24 24"><path fill="#fff" d="M12 2l3 7h7l-5.5 4.5 2 7.5-6.5-4.5-6.5 4.5 2-7.5L2 9h7z"/></svg></span></div>
  <h1>Professional Property<br>Management Backed by<br>Data. Driven by <span>Results.</span></h1>
  <p>Larkfield Ridge Management LLC helps property owners protect their investments while creating better experiences for tenants.</p>
  <div class="btn" style="left:92px;top:483px"><span class="txt">Explore Our Services</span><span class="star"><svg width="14" height="14" viewBox="0 0 24 24"><path fill="#fff" d="M12 2l3 7h7l-5.5 4.5 2 7.5-6.5-4.5-6.5 4.5 2-7.5L2 9h7z"/></svg></span></div>
  <svg class="abs" style="left:568px;top:640px" width="64" height="32" viewBox="0 0 64 32"><path d="M0 32 L32 4 L64 32 Z" fill="var(--red)"/><path d="M10 32 L32 13 L54 32 Z" fill="var(--light)"/></svg>
</section>

<!-- Features -->
<section class="features">
  <div class="feature" style="left:92px"><svg class="ic" viewBox="0 0 24 24"><circle cx="12" cy="12" r="9" fill="none" stroke="var(--red)" stroke-width="1.6"/><circle cx="12" cy="12" r="3.5" fill="none" stroke="var(--red)" stroke-width="1.6"/></svg>Data-Driven<br>Property Management<span class="corner"></span></div>
  <div class="feature" style="left:297px"><svg class="ic" viewBox="0 0 24 24"><path d="M3 11 12 3l9 8v10H3z" fill="none" stroke="var(--red)" stroke-width="1.6"/><rect x="9" y="14" width="6" height="7" fill="none" stroke="var(--red)" stroke-width="1.6"/></svg>Professional<br>Tenant Services<span class="corner"></span></div>
  <div class="feature" style="left:502px"><svg class="ic" viewBox="0 0 24 24"><circle cx="12" cy="12" r="9" fill="none" stroke="var(--red)" stroke-width="1.6"/><path d="M8 12h8M12 8v8" stroke="var(--red)" stroke-width="1.6"/></svg>Asset<br>Preservation Focus<span class="corner"></span></div>
  <div class="feature" style="left:707px"><svg class="ic" viewBox="0 0 24 24"><circle cx="12" cy="12" r="9" fill="none" stroke="var(--red)" stroke-width="1.6"/><path d="M7 12a5 5 0 0 0 10 0" fill="none" stroke="var(--red)" stroke-width="1.6"/></svg>Transparent<br>Communication<span class="corner"></span></div>
  <div class="feature" style="left:912px"><svg class="ic" viewBox="0 0 24 24"><path d="M12 2l8 3v6c0 5-3.5 9-8 11-4.5-2-8-6-8-11V5z" fill="none" stroke="var(--red)" stroke-width="1.6"/><path d="M8.5 12l2.5 2.5 4.5-5" fill="none" stroke="var(--red)" stroke-width="1.6"/></svg>Reliable Maintenance<br>Coordination<span class="corner"></span></div>
</section>

<!-- About -->
<section class="about-box">
  <div class="photo" role="img" aria-label="Handshake over a desk with a small model house and documents" style="left:12px;top:12px;width:568px;height:405px;background:linear-gradient(135deg,#2b3240 0%,#55606e 45%,#c9c4b8 75%,#8b7a62 100%)"></div>
  <div class="about-text">
    <div class="label">About Us</div>
    <h2>Your Trusted Partner in Property Management</h2>
    <p>Larkfield Ridge Management LLC is a real estate and property management firm. Our organization delivers comprehensive property management solutions that optimize asset performance and tenant satisfaction. By integrating advanced analytics with proven operational frameworks, our specialists ensure each property achieves sustained value appreciation.</p>
    <p>Drawing on decades of collective expertise, the team facilitates regulatory compliance, cost efficiency, and proactive maintenance.</p>
  </div>
  <div class="btn" style="left:628px;top:346px"><span class="txt">Learn More About Us</span><span class="star"><svg width="14" height="14" viewBox="0 0 24 24"><path fill="#fff" d="M12 2l3 7h7l-5.5 4.5 2 7.5-6.5-4.5-6.5 4.5 2-7.5L2 9h7z"/></svg></span></div>
</section>

<!-- Services -->
<section class="services">
  <div class="abs label center" style="top:68px">Services</div>
  <h2 class="abs heading center" style="top:88px">Complete Property Management Solutions</h2>
  <div class="arrow-circle" style="left:38px;top:1855px;top:365px"><svg width="18" height="12" viewBox="0 0 18 12"><path d="M17 6H2M6 1 1 6l5 5" fill="none" stroke="var(--ink)" stroke-width="1.5"/></svg></div>
  <div class="svc" style="left:92px;width:368px">
    <div class="photo" role="img" aria-label="Model of a red house with keys and blueprints" style="inset:0;background:linear-gradient(160deg,#7b2a2a 0%,#b9bcc4 50%,#e7eaee 100%)"></div>
    <div class="cap" style="background:var(--navy);height:75px;padding:14px 24px"><h3>Property Management</h3><p>Comprehensive day-to-day management that protects your investment while delivering exceptional service to tenants.</p></div>
  </div>
  <div class="svc" style="left:468px;width:367px">
    <div class="photo" role="img" aria-label="Agent handing documents to a client at a front door" style="inset:0;background:linear-gradient(120deg,#3b2c24 0%,#6a5b4f 45%,#2f3a4f 100%)"></div>
    <span class="corner-tl"></span>
    <div class="cap" style="background:linear-gradient(0deg,rgba(0,0,0,.55),rgba(0,0,0,0))"><h3>Tenant Placement</h3></div>
  </div>
  <div class="svc" style="left:843px;width:357px">
    <div class="photo" role="img" aria-label="Hands reviewing financial charts on paper" style="inset:0;background:linear-gradient(120deg,#cfd6dd 0%,#8f9aa6 55%,#3b4452 100%)"></div>
    <span class="corner-tl"></span>
    <div class="cap" style="background:linear-gradient(0deg,rgba(0,0,0,.55),rgba(0,0,0,0))"><h3>Financial Reporting</h3></div>
  </div>
  <div class="btn" style="left:511px;top:545px"><span class="txt">View All Services</span><span class="star"><svg width="14" height="14" viewBox="0 0 24 24"><path fill="#fff" d="M12 2l3 7h7l-5.5 4.5 2 7.5-6.5-4.5-6.5 4.5 2-7.5L2 9h7z"/></svg></span></div>
</section>

<!-- Why choose -->
<section class="why">
  <div class="bar"></div>
  <div class="photo" role="img" aria-label="Aerial view of apartment blocks and highways at sunset" style="left:30px;top:0;width:992px;height:455px;background:linear-gradient(100deg,#3e4a3a 0%,#6f7a5a 45%,#c9a263 75%,#eacb84 100%)"></div>
  <span class="corner-tr"></span>
  <div class="why-card">
    <div class="label">Why Choose Us</div>
    <h2>Why Choose Larkfield Ridge Management?</h2>
    <ul>
      <li>Proven data-driven management strategies</li>
      <li>Faster response times</li>
      <li>Professional tenant communication</li>
      <li>Preventative maintenance approach</li>
      <li>Transparent financial reporting</li>
      <li>Focus on long-term property value</li>
    </ul>
  </div>
</section>

<!-- Gallery -->
<section class="gallery">
  <div class="abs label center" style="top:62px">Gallery</div>
  <h2 class="abs heading center" style="top:80px">Featured Properties</h2>
  <div class="photo" role="img" aria-label="Aerial view of a green residential resort" style="left:0;top:150px;width:268px;height:405px;background:linear-gradient(180deg,#d4a567 0%,#7b8a5e 40%,#3f5a35 100%)"></div>
  <div class="photo" role="img" aria-label="Waterfront residential community with city skyline at sunset" style="left:278px;top:150px;width:607px;height:405px;background:linear-gradient(180deg,#c9b7a5 0%,#e0a06a 30%,#54636a 60%,#2f3c40 100%)">
    <span class="corner-tl"></span>
    <div style="position:absolute;left:0;right:0;bottom:0;height:95px;background:var(--navy);color:#fff;padding:18px 20px">
      <h3 style="font-size:19px">Residential Communities</h3>
      <p style="font-size:10px;line-height:14px;margin-top:4px;width:360px">Professional oversight, preventative maintenance, and consistent communication to keep communities running smoothly.</p>
      <svg style="position:absolute;right:16px;bottom:16px" width="30" height="12" viewBox="0 0 30 12"><path d="M0 6h28M23 1l5 5-5 5" fill="none" stroke="#fff" stroke-width="1.4"/></svg>
    </div>
  </div>
  <div class="photo" role="img" aria-label="Tall apartment buildings under a blue sky" style="left:895px;top:150px;width:305px;height:405px;background:linear-gradient(180deg,#5e93c9 0%,#a9c7e2 45%,#c8c2b0 75%,#7f8c62 100%)"><span class="corner-tl"></span></div>
  <div class="btn" style="left:459px;top:590px"><span class="txt">View All Properties</span><span class="star"><svg width="14" height="14" viewBox="0 0 24 24"><path fill="#fff" d="M12 2l3 7h7l-5.5 4.5 2 7.5-6.5-4.5-6.5 4.5 2-7.5L2 9h7z"/></svg></span></div>
</section>

<!-- FAQ -->
<section class="faq-box">
  <div class="faq-left">
    <div class="label">FAQ</div>
    <h2>Frequently Asked Questions</h2>
    <div class="faq-open"><h4>What types of properties do you manage?</h4><p>We manage residential and investment properties with customized management solutions.</p>
      <svg style="position:absolute;right:16px;top:18px" width="12" height="8" viewBox="0 0 12 8"><path d="M1 7l5-5 5 5" fill="none" stroke="#fff" stroke-width="1.5"/></svg></div>
    <div class="faq-item">How do you screen tenants?<svg width="12" height="8" viewBox="0 0 12 8"><path d="M1 1l5 5 5-5" fill="none" stroke="var(--navy)" stroke-width="1.5"/></svg></div>
    <div class="faq-item">How do you screen tenants?<svg width="12" height="8" viewBox="0 0 12 8"><path d="M1 1l5 5 5-5" fill="none" stroke="var(--navy)" stroke-width="1.5"/></svg></div>
    <div class="faq-item">How do owners receive financial reports?<svg width="12" height="8" viewBox="0 0 12 8"><path d="M1 1l5 5 5-5" fill="none" stroke="var(--navy)" stroke-width="1.5"/></svg></div>
    <div class="faq-item">How are maintenance requests handled?<svg width="12" height="8" viewBox="0 0 12 8"><path d="M1 1l5 5 5-5" fill="none" stroke="var(--navy)" stroke-width="1.5"/></svg></div>
  </div>
  <div style="position:absolute;left:422px;top:0;width:1px;height:100%;background:var(--line)"></div>
  <div class="photo" role="img" aria-label="Hand holding a small wooden house beside a question mark" style="left:436px;top:10px;width:570px;height:435px;background:linear-gradient(135deg,#e9ecef 0%,#c7c0b3 45%,#b07a4c 70%,#d8d4cf 100%)"><span class="corner-tr"></span></div>
</section>

<!-- Reviews -->
<div class="abs label center" style="top:3988px">Review</div>
<h2 class="abs heading center" style="top:4006px">Trusted by Property Owners &amp; Tenants</h2>
<div class="arrow-circle" style="left:42px;top:4147px"><svg width="18" height="12" viewBox="0 0 18 12"><path d="M17 6H2M6 1 1 6l5 5" fill="none" stroke="var(--ink)" stroke-width="1.5"/></svg></div>
<div class="arrow-circle" style="left:1120px;top:4147px"><svg width="18" height="12" viewBox="0 0 18 12"><path d="M1 6h15M12 1l5 5-5 5" fill="none" stroke="var(--ink)" stroke-width="1.5"/></svg></div>
<div class="review" style="left:92px"><span class="q">”</span><div class="who"><div class="av" role="img" aria-label="Reviewer avatar"></div><div><span>Property Owner</span><span class="stars">★★★★★</span></div></div><p>Larkfield Ridge Management has made owning rental properties stress-free. Their communication is excellent, maintenance is handled quickly, and I always know how my investment is performing.</p><span class="corner"></span></div>
<div class="review" style="left:436px"><span class="q">”</span><div class="who"><div class="av" role="img" aria-label="Reviewer avatar"></div><div><span>Residential Tenant</span><span class="stars">★★★★★</span></div></div><p>From the leasing process to ongoing support, the entire experience has been smooth. The team is responsive, organized, and genuinely cares about both owners and tenants.</p><span class="corner"></span></div>
<div class="review" style="left:780px"><span class="q">”</span><div class="who"><div class="av" role="img" aria-label="Reviewer avatar"></div><div><span>Investment Property Owner</span><span class="stars">★★★★★</span></div></div><p>Their proactive approach has reduced vacancies and kept our property in excellent condition. I highly recommend Larkfield Ridge Management to any real estate investor.</p><span class="corner"></span></div>

<!-- CTA -->
<section class="cta" role="img" aria-label="Wide view of a city with residential districts and green hills">
  <h2>Ready to Maximize<br>Your Property Investment?</h2>
  <p>Partner with Larkfield Ridge Management for reliable, professional property management focused on protecting your assets and improving tenant satisfaction.</p>
  <div class="btn" style="left:451px;top:195px"><span class="txt">Request Your Free Consultation Today</span><span class="star"><svg width="14" height="14" viewBox="0 0 24 24"><path fill="#fff" d="M12 2l3 7h7l-5.5 4.5 2 7.5-6.5-4.5-6.5 4.5 2-7.5L2 9h7z"/></svg></span></div>
</section>

<!-- Footer -->
<footer class="footer">
  <div class="abs logo" style="left:92px;top:112px;color:var(--navy)"><span class="mark"></span>LARKFIELD</div>
  <p class="abs" style="left:92px;top:175px;width:150px;font-size:10px;line-height:15px;color:var(--muted)">Larkfield Ridge Management LLC delivers professional real estate and property management services built on proven systems, transparent communication, and data-driven strategies.</p>
  <div class="abs" style="left:92px;top:300px;display:flex;gap:10px;align-items:center;font-size:12px;color:var(--navy-dark)">Follow us on <span class="icon" style="width:20px;height:20px;border:1px solid var(--ink);border-radius:50%"></span><span style="width:20px;height:20px;border:1px solid var(--ink);border-radius:50%"></span></div>
  <div class="abs links" style="left:362px;top:70px"><h4>Main Links</h4><a>Home</a><a>About Us</a><a>Services</a><a>Resources</a><a>FAQs</a><a>Contact Us</a></div>
  <div class="abs contact" style="left:622px;top:70px"><h4>Contact Us</h4>
    <div><span class="icon"><svg width="10" height="8" viewBox="0 0 10 8"><rect x=".5" y=".5" width="9" height="7" fill="none" stroke="var(--ink)"/><path d="M.5 .5 5 4.5 9.5.5" fill="none" stroke="var(--ink)"/></svg></span>info@larkfieldridgemanagement.com</div>
    <div><span class="icon"><svg width="10" height="10" viewBox="0 0 24 24"><path d="M6 2h4l2 5-3 2a12 12 0 0 0 6 6l2-3 5 2v4a2 2 0 0 1-2 2A18 18 0 0 1 4 4a2 2 0 0 1 2-2z" fill="var(--ink)"/></svg></span>555.014.2290</div>
  </div>
  <div class="abs" style="left:873px;top:70px"><h4>Subscribe NewsLetter</h4>
    <input type="text" placeholder="Enter Your Email">
    <div class="btn" style="position:relative;margin-top:14px;height:40px"><span class="txt" style="width:145px">Subscribe</span><span class="star" style="width:40px"><svg width="14" height="14" viewBox="0 0 24 24"><path fill="#fff" d="M12 2l3 7h7l-5.5 4.5 2 7.5-6.5-4.5-6.5 4.5 2-7.5L2 9h7z"/></svg></span></div>
  </div>
  <div class="abs" style="left:875px;top:308px;font-size:9px;color:var(--muted)">Privacy Policy | Cookie Policy | Terms and Conditions</div>
  <div class="abs" style="left:0;top:335px;width:1200px;height:1px;background:var(--line)"></div>
  <div class="abs center" style="top:348px;font-size:9px;color:var(--muted)">© 2026 Larkfield Ridge Management LLC. All Rights Reserved.</div>
</footer>

</body>
</html>
```